Corvane Grid Works Ltd. -Website Design

We need a site design for a new company based in Toronto, Ontario called 'Corvane Grid Works Ltd.'

We provide Engineering services, Subsurface Utility Engineering services and Geospatial Data Management.

Our clients are typically Utilities (electric, gas, water/waste water, telcom) or contractors/consultants working on their behalf.

Our business model is new and we are the first to offer all three services to our clients; this allows us to provide value-added services from all three of our main offerings.

Target Market(s)

Field Supervisors, Managers, Directors, VP's at Utility companies

Industry/Entity Type

Business

Requirements
Must have
• -The landing page must clearly identify the 3 main business offerings allowing the user to easily navigate to each....Utility Engineering, GIS Data Management & Sub-surface Utility Engineering (SUE).

-Interactive contact page with integrated email

-based on existing logo design...
Nice to have
• -Ability to easily add/post news releases, updates, jobs, etc...

-Ability to integrate instructional YouTube video(s)

Should not have
• -Cannot be too cluttered....

```html
<!DOCTYPE html>
<html lang="en">
<head>
<meta charset="utf-8">
<title>Corvane Grid Works Ltd. – Home</title>
<link rel="stylesheet" href="https://fonts.googleapis.com/css2?family=Open+Sans:wght@400;600&family=Arimo:wght@400;700&family=PT+Sans:wght@400;700&display=swap">
<style>
:root{
  --page:#e6e6e6;
  --ink:#1d1d1d;
  --blue-title:#1f4f8f;
  --red:#c2331a;
  --bullet:#2d6fc0;
  --line:#8a8a8a;
  --footer:#f3f4f4;
  --white:#ffffff;
}
*{box-sizing:border-box;margin:0;padding:0}
html,body{width:693px;height:1200px;overflow:hidden}
body{background:var(--page);font-family:"PT Sans",sans-serif;color:var(--ink);position:relative}
.abs{position:absolute}
.header-band{left:0;top:0;width:693px;height:100px;background:linear-gradient(#ffffff,#ececec)}
.hero{left:0;top:96px;width:693px;height:292px}
.nav{left:13px;top:73px;display:flex;align-items:flex-end;font-family:"Open Sans",sans-serif}
.nav a{font-size:14.5px;color:#111;text-decoration:none;margin-right:32px;padding:0 4px 5px}
.nav a.active{background:var(--red);color:var(--white);border-radius:6px 6px 0 0;padding:5px 18px 6px;margin-right:20px}
.logo-card{left:404px;top:0;width:289px;height:185px}
.brand{left:452px;top:30px;display:flex;align-items:center;gap:10px}
.brand-mark{width:26px;height:26px;background:#d04020;border-radius:50%}
.brand-name{font-family:"Open Sans",sans-serif;font-weight:600;font-size:19px;color:#333;line-height:1.1}
.offer{top:411px;width:187px;height:244px;background:#444}
.offer h2{height:36px;line-height:36px;text-align:center;color:var(--white);font-family:"Open Sans",sans-serif;font-weight:600;font-size:14px;letter-spacing:.3px}
.offer .photo{height:208px;border-top:1px solid #fff}
.offer .caption{position:absolute;left:0;bottom:0;width:100%;height:70px;background:rgba(20,20,20,.72);padding:4px 7px;color:var(--white);font-family:"Open Sans",sans-serif;font-size:8.6px;line-height:12.5px}
.offer .more{position:absolute;left:50%;transform:translateX(-50%);bottom:6px;width:73px;height:18px;border-radius:8px;background:linear-gradient(#f4f4f4,#bcbcbc);color:#222;font-size:7.5px;text-align:center;line-height:18px}
.offer-eng{left:55px}.offer-eng h2{background:linear-gradient(#d23a1c,#b3250f)}
.offer-gis{left:250px}.offer-gis h2{background:linear-gradient(#d99a1a,#b87b0a)}
.offer-sue{left:445px}.offer-sue h2{background:linear-gradient(#4a89c8,#2a64a6)}
.field-photo{left:22px;top:693px;width:208px;height:156px;background:var(--white);padding:4px}
.field-photo div{width:100%;height:100%;background:linear-gradient(#7aa05a,#8d9076 60%,#a9a9a3)}
.section-title{color:var(--blue-title);font-size:13px;font-weight:400;white-space:nowrap;line-height:16px}
.services-title{font-family:"Arimo",sans-serif;font-size:13.5px}
.list{list-style:none;font-size:9.3px;line-height:15.6px;white-space:nowrap}
.list li{position:relative;padding-left:16px}
.list li::before{content:"";position:absolute;left:0;top:5px;border-left:5px solid var(--bullet);border-top:3px solid transparent;border-bottom:3px solid transparent}
.list li.cont::before{display:none}
.list.gis{line-height:14px}
.list.gis li::before{top:4px}
.list.sue li{padding-left:8px}
.form-label{left:496px;font-size:8.6px;line-height:10px}
.form-field{left:496px;width:138px;height:17px;background:var(--white);border:1px solid var(--line)}
.form-area{height:82px}
.submit{left:586px;top:898px;width:47px;height:15px;border:1px solid #666;border-radius:2px;background:linear-gradient(#fafafa,#cfcfcf);font-size:9px;font-weight:700;text-align:center;line-height:13px}
.footer-wave{left:0;top:1040px;width:693px;height:160px}
.footer-links{left:19px;top:1140px;font-size:9.8px}
.cards{left:19px;top:1171px;display:flex;gap:5px}
.cards span{width:29px;height:18px;border-radius:2px}
.copyright{left:0;width:693px;text-align:center;top:1180px;font-size:8.4px}
.social{left:545px;top:1163px;display:flex;gap:9px}
.social span{width:26px;height:27px;border-radius:4px;border:2px solid #9aa}
</style>
</head>
<body>
<div class="abs header-band"></div>

<svg class="abs hero" viewBox="0 0 693 292" role="img" aria-label="Engineer's hands drafting on a utility blueprint with pencil and compass">
  <defs><linearGradient id="bp" x1="0" y1="0" x2="1" y2="1"><stop offset="0" stop-color="#c9d6ea"/><stop offset=".5" stop-color="#e7edf7"/><stop offset="1" stop-color="#b8c8e0"/></linearGradient></defs>
  <path d="M0 0H693V244C560 250 440 265 300 282C180 296 80 300 0 286Z" fill="url(#bp)"/>
  <path d="M0 286C80 300 180 296 300 282C440 265 560 250 693 244" fill="none" stroke="#fff" stroke-width="4"/>
</svg>

<svg class="abs logo-card" viewBox="0 0 289 185" aria-hidden="true">
  <path d="M4 0H289V185C220 160 120 140 20 126Z" fill="#fafafa" stroke="#bbb"/>
</svg>
<div class="abs brand"><span class="brand-mark"></span><span class="brand-name">Corvane Grid Works</span></div>

<nav class="abs nav"><a class="active" href="#">Home</a><a href="#">Services</a><a href="#">Contact Us</a></nav>

<section class="abs offer offer-eng"><h2>UTILITY ENGINEERING</h2>
  <div class="photo" role="img" aria-label="Vacuum excavation truck at a utility site" style="background:linear-gradient(#b8cde6,#d9dde2 55%,#7a7a72)"></div>
  <div class="caption">Lorem Ipsum is simply dummy text of the printing and typesetting industry.Lorem Ipsum is simply dummy text of the printing<span class="more">READ MORE</span></div></section>
<section class="abs offer offer-gis"><h2>GIS DATA MANAGEMENT</h2>
  <div class="photo" role="img" aria-label="Close-up of server drive bays" style="background:linear-gradient(135deg,#2a2218,#8a7250 50%,#3a2c1a)"></div>
  <div class="caption">Lorem Ipsum is simply dummy text of the printing and typesetting industry.Lorem Ipsum is simply dummy text of the printing<span class="more">READ MORE</span></div></section>
<section class="abs offer offer-sue"><h2>SUE</h2>
  <div class="photo" role="img" aria-label="Field worker in hard hat locating buried utilities beside a pedestal" style="background:linear-gradient(#c8c4b4,#b5aa90 60%,#8f8a78)"></div>
  <div class="caption">Lorem Ipsum is simply dummy text of the printing and typesetting industry.Lorem Ipsum is simply dummy text of the printing<span class="more">READ MORE</span></div></section>

<div class="abs field-photo"><div role="img" aria-label="Crew working at an open manhole beside a utility trailer"></div></div>

<h3 class="abs section-title services-title" style="left:248px;top:695px">Utility Engineering Services</h3>
<ul class="abs list" style="left:248px;top:720px">
  <li>&nbsp;Project Management;</li><li>Outside Plant Network Design;</li><li>Utility Design and Permitting;</li><li>Project Management;</li><li>Surveys and Mapping (GPS);</li><li>Pole line design and attachment permitting</li><li class="cont">(Pole Load Calculations);</li><li>Specialty Permits for the Utility Industry</li><li class="cont">(Railway, PTA, Conservation Authority);</li><li>Manhole and Duct Bank Design.</li>
</ul>

<form class="contact-form">
  <div class="abs form-label" style="top:682px">Name :</div><div class="abs form-field" style="top:697px"></div>
  <div class="abs form-label" style="top:722px">Phone :</div><div class="abs form-field" style="top:734px"></div>
  <div class="abs form-label" style="top:759px">Email :</div><div class="abs form-field" style="top:774px"></div>
  <div class="abs form-label" style="top:795px">Comment :</div><div class="abs form-field form-area" style="top:806px"></div>
</form>
<div class="abs submit">Submit</div>

<h3 class="abs section-title" style="left:26px;top:923px">Geographic Information Systems (GIS) Services</h3>
<ul class="abs list gis" style="left:26px;top:948px">
  <li>GIS Project Management</li><li>Records Conversion for GIS Systems</li><li>Landbase Data Management</li><li>Data Translation and Transformation Between File Formats</li><li>Hydro Asset Management using Geomark</li><li>Spatial Data Analysis &amp; Manipulation</li><li>Fibre Asset Management using Geomark &amp; LineTrace Software</li><li>Custom Cartographic Mapping</li><li>Engineering and Base Mapping using Geomark, DraftCore, MapLedger</li><li>Geomark Customization &amp; Application Development</li><li>Database Development.</li>
</ul>

<h3 class="abs section-title" style="left:361px;top:923px">Subsurface Utility Engineering (SUE) Services</h3>
<ul class="abs list sue" style="left:361px;top:951px">
  <li>Project Management</li><li>Consulting</li><li>Surveying</li><li>CAD Processing of Results</li>
</ul>

<svg class="abs footer-wave" viewBox="0 0 693 160" aria-hidden="true">
  <path d="M0 86C250 80 450 22 693 24V160H0Z" fill="var(--footer)"/>
  <path d="M0 86C250 80 450 22 693 24" fill="none" stroke="#fff" stroke-width="5"/>
</svg>

<div class="abs footer-links">Home | Services | Contact Us</div>
<div class="abs cards"><span style="background:#e8e8e8;border:1px solid #bbb"></span><span style="background:#f0f0f0;border:1px solid #bbb"></span><span style="background:#2a4a9a"></span><span style="background:#1c5a9a"></span></div>
<div class="abs copyright">© 2012 corvanegrid.ca. All Rights Reserved.</div>
<div class="abs social"><span style="background:#3a68b0"></span><span style="background:#7cc0e8"></span><span style="background:#e89a2a"></span></div>
</body>
</html>
```